Corporate Business Card

Very professional, Modern, Not to busy, include phone address email, website
(253) 617-4930, 18761 52nd Avenue S, Kent, WA 98047, martin@plumlinegroup.com, varkoworks.com

Target Market(s)

Manufacturing

Industry/Entity Type

Aero, machining, manufacturing, Off road racing

Contact Information for Business Card

Phone, address email, website

```html
<!DOCTYPE html>
<html lang="en">
<head>
<meta charset="utf-8">
<title>Varko Works – Business Card</title>
<link href="https://fonts.googleapis.com/css2?family=Montserrat:wght@400;500;700&display=swap" rel="stylesheet">
<style>
  :root {
    --navy: #173566;
    --red: #d9262c;
    --silver: #c9ccd1;
    --white: #ffffff;
    --ink: #1b1b1f;
    --backdrop: #e9e6e1;
  }
  * { box-sizing: border-box; margin: 0; padding: 0; }
  html, body {
    width: 1200px; height: 1023px; overflow: hidden;
    background: var(--backdrop);
    font-family: "Montserrat", sans-serif;
  }
  .sheet {
    position: relative; width: 1200px; height: 1023px;
  }
  .card {
    position: absolute; width: 620px; height: 354px;
    border-radius: 22px; overflow: hidden;
    box-shadow: 0 6px 18px rgba(0,0,0,.18);
  }
  .card--front { left: 120px; top: 90px; background: var(--navy); }
  .card--back  { left: 460px; top: 540px; background: var(--white); }

  .wordmark {
    position: absolute; font-weight: 700; letter-spacing: 1px; white-space: nowrap;
  }
  .card--front .wordmark {
    left: 130px; top: 120px; font-size: 58px; color: var(--silver);
  }
  .card--front .rule {
    position: absolute; left: 130px; top: 210px; width: 360px; height: 2px;
    background: var(--silver);
  }
  .card--back .wordmark {
    right: 40px; top: 50px; font-size: 38px; color: var(--navy);
  }
  .card--back .rule {
    position: absolute; right: 180px; top: 112px; width: 240px; height: 2px;
    background: var(--navy);
  }

  .address {
    position: absolute; left: 44px; top: 150px;
    font-size: 15px; line-height: 1.45; color: var(--ink); font-weight: 500;
  }
  .contacts {
    position: absolute; left: 44px; top: 218px; list-style: none;
    font-size: 15px; line-height: 1; color: var(--ink); font-weight: 500;
  }
  .contacts li { display: flex; align-items: center; gap: 10px; margin-bottom: 9px; }
  .contacts svg { width: 15px; height: 15px; fill: var(--red); flex: none; }

  .band { position: absolute; left: 0; bottom: 0; width: 620px; height: 70px; }
</style>
</head>
<body>
<main class="sheet">

  <section class="card card--front" aria-label="Card front">
    <div class="wordmark">Varko Works</div>
    <div class="rule"></div>
  </section>

  <section class="card card--back" aria-label="Card back">
    <div class="wordmark">Varko Works</div>
    <div class="rule"></div>

    <p class="address">18761 52nd Avenue<br>S, Kent, WA 98047</p>

    <ul class="contacts">
      <li>
        <svg viewBox="0 0 16 16" aria-hidden="true"><path d="M3 1l3 3-1.5 2a9 9 0 0 0 5.5 5.5L12 10l3 3-2 2C6 15 1 10 1 3z"/></svg>
        (253) 617-4930
      </li>
      <li>
        <svg viewBox="0 0 16 16" aria-hidden="true"><path d="M1 3h14v10H1z M1 3l7 6 7-6" stroke="#fff" stroke-width="1"/></svg>
        martin@plumlinegroup.com
      </li>
      <li>
        <svg viewBox="0 0 16 16" aria-hidden="true"><circle cx="8" cy="8" r="7"/><path d="M1 8h14M8 1c3 3 3 11 0 14M8 1c-3 3-3 11 0 14" stroke="#fff" stroke-width="1" fill="none"/></svg>
        www.varkoworks.com
      </li>
    </ul>

    <svg class="band" viewBox="0 0 620 70" aria-hidden="true">
      <rect x="0" y="36" width="178" height="8" fill="var(--red)"/>
      <rect x="184" y="36" width="180" height="8" fill="var(--navy)"/>
      <polygon points="370,36 560,36 566,44 370,44" fill="var(--red)"/>
      <polygon points="0,50 572,50 596,14 620,14 620,70 0,70" fill="var(--navy)"/>
    </svg>
  </section>

</main>
</body>
</html>
```